Professional Photography Business cards

I need business cards that include my logo which I have uploaded. I run a photography business. I am open to ideas but I would like one side to have my logo and the other side to have my contact info. I don't have a website made but I do own a website domain. I have uploaded 2 different logo color schemes. My business colors are Blue, black , and white.

Business Name
Business Phone Number
Business Email
Business Website address
Instagram

Industry/Entity Type

Professional Photography

Contact Information for Business Card

Phone Number: 916-384-7702 email: info@tlane-studio.example Instagram: @t.lanestudio website doman- www.tlane-studio.example

Requirements
Must have
• I like the idea of a business card with a full black background front and back of card. My colors must include royal blue, black, and white

```html
<!DOCTYPE html>
<html lang="en">
<head>
<meta charset="utf-8">
<title>T. Lane Studio – Business Cards</title>
<link rel="stylesheet" href="https://fonts.googleapis.com/css2?family=Montserrat:wght@400;500&display=swap">
<style>
  :root {
    --backdrop: #b9b9b9;
    --card-black: #000000;
    --card-white: #ffffff;
    --royal-blue: #1a1aa6;
    --ink: #111111;
    --soft-grey: #e6e6e6;
    --card-shadow: rgba(0, 0, 0, 0.35);
  }
  * { box-sizing: border-box; margin: 0; padding: 0; }
  html, body {
    width: 1200px; height: 900px; overflow: hidden;
    background: var(--backdrop);
    font-family: "Montserrat", Arial, sans-serif;
  }
  .stage {
    position: relative; width: 1200px; height: 900px;
    display: flex; flex-direction: column; align-items: center; justify-content: center; gap: 40px;
  }
  .card {
    position: relative; width: 640px; height: 366px;
    border-radius: 26px; overflow: hidden;
    box-shadow: 0 10px 24px var(--card-shadow);
  }
  .card--front { background: var(--card-black); }
  .card--back { background: var(--card-white); }

  .brand { position: absolute; text-align: center; }
  .brand__name {
    font-weight: 500; color: var(--royal-blue);
    font-size: 50px; letter-spacing: 1px; line-height: 1;
  }
  .brand__tagline {
    margin-top: 12px; font-weight: 400; font-size: 14px;
    letter-spacing: 12px; text-transform: uppercase;
  }
  .card--front .brand { left: 0; right: 0; top: 130px; }
  .card--front .brand__tagline { color: var(--card-white); }
  .card--back .brand { left: 70px; top: 86px; text-align: left; }
  .card--back .brand__tagline { color: var(--ink); }

  .deco-circle { position: absolute; right: -40px; top: -30px; }

  .contact-list {
    position: absolute; left: 56px; bottom: 46px;
    list-style: none; display: flex; flex-direction: column; gap: 12px;
  }
  .contact-item {
    display: flex; align-items: center; gap: 12px;
    font-size: 17px; color: var(--ink);
  }
  .contact-item__icon {
    width: 24px; height: 24px; border-radius: 50%;
    background: var(--royal-blue); display: flex; align-items: center; justify-content: center;
  }
  .contact-item--web .accent { color: var(--royal-blue); }

  .social-handle {
    position: absolute; right: 40px; bottom: 56px;
    display: flex; align-items: center; gap: 10px;
    font-size: 16px; color: var(--ink);
  }
  .social-handle__dot {
    width: 20px; height: 20px; border-radius: 50%; background: var(--royal-blue);
  }
</style>
</head>
<body>
<main class="stage">
  <section class="card card--front" aria-label="Business card front">
    <div class="brand">
      <p class="brand__name">T. Lane Studio</p>
      <p class="brand__tagline">Photography</p>
    </div>
  </section>

  <section class="card card--back" aria-label="Business card back">
    <svg class="deco-circle" width="300" height="300" viewBox="0 0 300 300" aria-hidden="true">
      <circle cx="150" cy="150" r="130" fill="none" stroke="var(--soft-grey)" stroke-width="26"/>
    </svg>

    <div class="brand">
      <p class="brand__name">T. Lane Studio</p>
      <p class="brand__tagline">Photography</p>
    </div>

    <ul class="contact-list">
      <li class="contact-item">
        <span class="contact-item__icon">
          <svg width="13" height="13" viewBox="0 0 24 24" aria-hidden="true">
            <path d="M6.6 10.8a15 15 0 0 0 6.6 6.6l2.2-2.2a1 1 0 0 1 1-.25 11.4 11.4 0 0 0 3.6.57 1 1 0 0 1 1 1V20a1 1 0 0 1-1 1A17 17 0 0 1 3 4a1 1 0 0 1 1-1h3.5a1 1 0 0 1 1 1c0 1.25.2 2.45.57 3.57a1 1 0 0 1-.25 1z" fill="#fff"/>
          </svg>
        </span>
        916-384-7702
      </li>
      <li class="contact-item">
        <span class="contact-item__icon">
          <svg width="14" height="14" viewBox="0 0 24 24" aria-hidden="true">
            <rect x="3" y="6" width="18" height="12" rx="1.5" fill="none" stroke="#fff" stroke-width="2"/>
            <path d="M3 7l9 6 9-6" fill="none" stroke="#fff" stroke-width="2"/>
          </svg>
        </span>
        info@tlane-studio.example
      </li>
      <li class="contact-item contact-item--web">
        <span class="contact-item__icon">
          <svg width="14" height="14" viewBox="0 0 24 24" aria-hidden="true">
            <circle cx="12" cy="12" r="9" fill="none" stroke="#fff" stroke-width="2"/>
            <ellipse cx="12" cy="12" rx="4" ry="9" fill="none" stroke="#fff" stroke-width="1.6"/>
            <path d="M3 12h18" stroke="#fff" stroke-width="1.6"/>
          </svg>
        </span>
        <span>www.<span class="accent">tlane-studio</span>.example</span>
      </li>
    </ul>

    <div class="social-handle">
      <span>@t.lanestudio</span>
      <span class="social-handle__dot" aria-hidden="true"></span>
    </div>
  </section>
</main>
</body>
</html>
```